Mortgage Company ready to make a statement!

We have a basic logo that I am fairly happy with ... but it could use a little bit of tweaking before we order the sign for our building. We also want some knock-your-socks-off business cards.
Problem: Inside of our Mortgage Office (Bright Fern Mortgage Group), we are going to have a coffee lounge (Sunbrew Cafe) for Realtors to use instead of the local Cuppington to meet with homebuyers. The office and coffee lounge are in an industrial building and is decorated with cozy overstuffed chairs, a hodge podge of interesting lamps and furniture, and goal is to make it as inviting as possible. However, we are a financial institution... so we need to keep it pretty clean as well.
One of my favorite marketing ideas is to cut a house key for everyone who buys a home using us with a key that matches our logo. There's only one key shape that works really well, so that needs to match the logo in order for the idea to work. I'll attach an image of the key blank.... although the way the key hole cut out looks terrible, so I was thinking of having them just do a thin outline instead.
Would like a similar, matching logo for the Sunbrew Cafe... but possibly something that would be a little less formal and would be cute on a coffee mug- nothing stuffy.
AND, we're opening a home inspection company as well, and we would like that logo and branding to match. The home inspection company is "Bright Fern Home Inspections"
We were thinking that for the home inspection company , we could use a magnifying glass shape inside of the house shape for the logo, use a keyhole shape inside of the same house for the mortgage company, and use a coffee cup inside of the house shape for Sunbrew Cafe.
Just getting stuck and need to help. I designed the attached logo myself, and that is what we are currently using. Designers at local printing companies have failed to impress us.
The mortgage industry has a lot of numbers and logos, etc that they require us to put on our business cards... so it's hard to keep them looking clean.
HELP! HELP! :)

```html
<!DOCTYPE html>
<html lang="en">
<head>
<meta charset="utf-8">
<title>Bright Fern Mortgage Group – Business Cards</title>
<link href="https://fonts.googleapis.com/css2?family=Montserrat:wght@400;600&display=swap" rel="stylesheet">
<style>
  :root {
    --brand-blue: #23658a;
    --ink: #4a4752;
    --paper: #ffffff;
    --backdrop: #eeece6;
    --white: #ffffff;
  }
  * { box-sizing: border-box; margin: 0; padding: 0; }
  html, body {
    width: 1200px; height: 929px; overflow: hidden;
    background: var(--backdrop);
    font-family: "Montserrat", sans-serif;
  }
  .stage {
    width: 1200px; height: 929px;
    display: flex; flex-direction: column;
    align-items: center; justify-content: center; gap: 40px;
  }
  .card {
    width: 700px; height: 400px; position: relative; overflow: hidden;
  }
  .card-back {
    background: var(--brand-blue);
    display: flex; align-items: center; justify-content: center;
  }
  .wordmark {
    font-weight: 400; line-height: 1.1; text-align: left;
    display: flex; align-items: center; gap: 18px;
  }
  .wordmark-dot {
    width: 22px; height: 22px; border-radius: 50%; background: currentColor; flex: none;
  }
  .wordmark-name { font-size: 44px; letter-spacing: 1px; }
  .wordmark-sub  { font-size: 30px; }
  .card-back .wordmark { color: var(--white); }

  .card-front { background: var(--paper); }
  .card-front .wordmark {
    color: var(--brand-blue);
    position: absolute; left: 0; right: 0; top: 70px; justify-content: center;
  }
  .contact-band {
    position: absolute; left: 0; right: 0; bottom: 0; height: 150px;
    background: var(--brand-blue);
    border-top: 6px solid var(--paper);
    box-shadow: 0 -3px 0 var(--ink);
    display: flex; align-items: center; padding: 0 50px;
    color: var(--white);
  }
  .person { text-align: right; width: 250px; padding-right: 26px; }
  .person-name { font-weight: 600; font-size: 24px; letter-spacing: 1.5px; }
  .person-role { font-weight: 600; font-size: 16px; letter-spacing: 1px; margin-top: 4px; }
  .divider { width: 2px; height: 90px; background: var(--white); }
  .contact-list { list-style: none; padding-left: 26px; font-size: 15px; letter-spacing: 0.5px; }
  .contact-list li { display: flex; align-items: center; gap: 12px; line-height: 24px; }
  .contact-list svg { width: 13px; height: 13px; fill: var(--white); flex: none; }
</style>
</head>
<body>
<main class="stage">
  <section class="card card-back" aria-label="Business card back">
    <div class="wordmark">
      <span class="wordmark-dot"></span>
      <div>
        <div class="wordmark-name">BRIGHT FERN</div>
        <div class="wordmark-sub">Mortgage Group</div>
      </div>
    </div>
  </section>

  <section class="card card-front" aria-label="Business card front">
    <div class="wordmark">
      <span class="wordmark-dot"></span>
      <div>
        <div class="wordmark-name">BRIGHT FERN</div>
        <div class="wordmark-sub">Mortgage Group</div>
      </div>
    </div>
    <div class="contact-band">
      <div class="person">
        <div class="person-name">DANA MERROW</div>
        <div class="person-role">CEO</div>
      </div>
      <div class="divider"></div>
      <ul class="contact-list">
        <li><svg viewBox="0 0 16 16"><path d="M3 1l3 3-2 2c1 2 4 5 6 6l2-2 3 3-2 2C7 15 1 9 1 3z"/></svg>555-204-7731</li>
        <li><svg viewBox="0 0 16 16"><path d="M4 0h8v16H4zM5.5 2v10h5V2z"/></svg>555-310-8842</li>
        <li><svg viewBox="0 0 16 16"><path d="M4 0h8v5H4zM1 6h14v7h-3v3H4v-3H1zM5 11v4h6v-4z"/></svg>555-310-8842</li>
        <li><svg viewBox="0 0 16 16"><path d="M0 3h16v1L8 9 0 4zM0 6l8 5 8-5v7H0z"/></svg>dana.merrow@brightfernmail.com</li>
      </ul>
    </div>
  </section>
</main>
</body>
</html>
```